Clearvale glass & hardware manufacturer

Need a SEO friendly, modern & professional looking website. We are selling all kinds of glass & accessories ( Glass/ Mirror/ splash back/ pool fence/ balustrade/ hardware...we are specialised on some special glass, like curve glass,tinted glass thermal & accoustic glass...) It should has simple & crisp feeling like a glass. It must be fully functional with product display and online ordering. Please see attached confirmed logo design(Blue & white). Make sure the theme color match its feel.

Target Market(s)

Architect and designer, Builder, & Developer

Industry/Entity Type

Manufacturer

Coding

Coded - Design and coding required

Font styles to use
Serif
Sans Serif

Colors

Designer to choose colors to be used in the design.

Requirements
Must have
• Glass & hardware theme and our logo
• Here are some competitor's website for reference. (Borrow ideas but not copy : )
• 1.https://www.tarvino.com.au/about
• 2.http://www.plumeretail.com.au/
• 3.http://www.kwd.com.au/
• 4.http://www.brackenhillfittings.com.au/
Nice to have
• Some transparent or semi transparent effects to make the website like a glass
Should not have
• No limitation for your imagination

```html
<!DOCTYPE html>
<html lang="en">
<head>
<meta charset="utf-8">
<title>Clearvale Glass &amp; Hardware</title>
<link href="https://fonts.googleapis.com/css2?family=Exo+2:wght@500;600&family=Nunito+Sans:wght@400;600;700&family=Open+Sans:wght@400;600&display=swap" rel="stylesheet">
<style>
:root{
  --blue:#1e9ad6;
  --blue-deep:#1565b0;
  --blue-band:rgba(30,140,210,.82);
  --ink:#1d1d1d;
  --muted:#555;
  --line:#c9c9c9;
  --white:#fff;
  --foot-bar:#d9d9d9;
}
*{margin:0;padding:0;box-sizing:border-box}
html,body{width:1200px;height:2913px;overflow:hidden}
body{position:relative;font-family:'Open Sans',sans-serif;color:var(--ink);background:var(--white)}
.abs{position:absolute}
a{color:inherit;text-decoration:none}

/* top bar */
.top-bar{left:0;top:0;width:1200px;height:30px;background:var(--blue);color:var(--white);font-size:11px;font-weight:600}
.top-bar .item{position:absolute;top:8px;display:flex;align-items:center;gap:6px}
.top-bar svg{width:14px;height:14px}

/* header */
.site-header{left:0;top:30px;width:1200px;height:110px;background:var(--white)}
.brand{display:flex;align-items:center;gap:12px}
.brand-mark{width:46px;height:46px;background:var(--blue-deep)}
.brand-name{font-family:'Nunito Sans',sans-serif;font-weight:700;font-size:30px;color:var(--blue-deep);letter-spacing:1px}
.site-header .brand{position:absolute;left:113px;top:32px}
.main-nav{position:absolute;top:53px;left:0;font-family:'Nunito Sans',sans-serif;font-size:15px;color:#333;text-transform:uppercase}
.main-nav a{position:absolute;white-space:nowrap}
.main-nav a.active{color:var(--blue)}

/* hero */
.hero{left:0;top:140px;width:1200px;height:569px;background:linear-gradient(180deg,#c9d6e0 0%,#eef2f5 35%,#b8c3cc 60%,#8f9aa3 100%)}
.hero-hex{left:120px;top:175px;width:400px;height:465px}
.hero-title{left:120px;top:295px;width:400px;font-family:'Exo 2',sans-serif;font-weight:500;font-size:54px;line-height:63px;color:var(--white);padding-left:58px;text-transform:uppercase}
.hero-dots{left:554px;top:650px;display:flex;gap:9px}
.hero-dots span{width:14px;height:14px;border-radius:50%;background:#111}
.hero-dots span.on{background:var(--white);border:2px solid #111}

/* section headings */
.section-title{left:0;width:1200px;text-align:center;font-family:'Nunito Sans',sans-serif;font-weight:600;font-size:27px;color:var(--ink);text-transform:uppercase}
.title-rule{left:438px;width:324px;height:20px}

/* special glass */
.glass-card{top:833px;width:307px;height:287px}
.card-label{position:absolute;left:0;right:0;height:46px;background:var(--blue-band);color:var(--white);font-family:'Nunito Sans',sans-serif;font-size:20px;text-align:center;line-height:46px;text-transform:uppercase}

/* about */
.about{left:0;top:1185px;width:1200px;height:479px;background:linear-gradient(100deg,#bcd9ee 0%,#2f7fc4 35%,#1c6db4 60%,#2a8ed2 100%)}
.about-copy{left:732px;top:1290px;width:360px;color:var(--white)}
.about-copy h2{font-family:'Nunito Sans',sans-serif;font-weight:600;font-size:30px;line-height:34px;text-transform:uppercase}
.about-copy h3{font-family:'Nunito Sans',sans-serif;font-weight:600;font-size:23px;line-height:28px;text-transform:uppercase}
.about-copy p{font-size:13.5px;line-height:19px;margin-top:14px;color:#dcebf7}
.btn{display:block;width:161px;height:43px;line-height:43px;text-align:center;font-family:'Nunito Sans',sans-serif;font-size:16px;text-transform:uppercase}
.btn-light{background:var(--white);color:var(--blue)}
.btn-blue{background:var(--blue);color:var(--white)}

/* hardware */
.hardware{left:0;top:1664px;width:1200px;height:443px;background:linear-gradient(180deg,#f4f8fb 0%,#e6eef4 100%)}
.product-card{top:1822px;width:218px;height:231px}
.product-card .card-label{height:46px;line-height:46px;font-size:17px}
.slider-arrow{top:1904px;width:40px;height:70px}

/* why */
.why{left:0;top:2107px;width:1200px;height:427px;background:linear-gradient(180deg,#8fc1e8 0%,#c9e2f4 55%,#eef6fc 100%)}
.why-copy{left:153px;top:2196px;width:360px}
.why-copy h2{font-family:'Nunito Sans',sans-serif;font-weight:600;font-size:27px;text-transform:uppercase;margin-bottom:14px}
.why-copy p{font-size:13.5px;line-height:20px;color:var(--ink);margin-bottom:12px}
.why-visual{left:650px;top:2140px;width:460px;height:380px;background:linear-gradient(135deg,rgba(255,255,255,.7),rgba(170,200,215,.55));border-radius:4px}

/* footer */
.site-footer{left:0;top:2534px;width:1200px;height:311px;background:var(--white)}
.site-footer .brand{position:absolute;left:132px;top:80px}
.social{position:absolute;left:140px;top:174px;display:flex;gap:2px}
.social span{width:42px;height:42px;border-radius:50%;background:var(--blue-deep)}
.foot-col{position:absolute;top:80px;font-size:15px;color:#555}
.foot-col h4{font-family:'Nunito Sans',sans-serif;font-weight:700;font-size:18px;color:var(--blue-deep);text-transform:uppercase;margin-bottom:14px}
.foot-col li{list-style:none;height:30.5px;display:flex;align-items:center;gap:12px}
.foot-col svg{width:15px;height:15px;flex:none}
.copyright{left:0;top:2845px;width:1200px;height:68px;background:var(--foot-bar);text-align:center;line-height:68px;font-size:13px;color:#444}
</style>
</head>
<body>

<div class="abs top-bar">
  <span class="item" style="left:130px"><svg viewBox="0 0 16 16"><circle cx="6.5" cy="6.5" r="4.5" fill="none" stroke="#fff" stroke-width="2"/><path d="M10 10l4.5 4.5" stroke="#fff" stroke-width="2.2"/></svg>SEARCH HERE</span>
  <span class="item" style="left:672px"><svg viewBox="0 0 16 16"><path d="M4 1l3 3-2 2c1 2 3 4 5 5l2-2 3 3-2 2C7 14 2 9 2 3z" fill="#fff"/></svg>CALL US TODAY: 555-010-4471</span>
  <span class="item" style="left:905px"><svg viewBox="0 0 16 16"><rect x="1" y="3" width="14" height="10" fill="#fff"/><path d="M1 3l7 6 7-6" fill="none" stroke="#1e9ad6" stroke-width="1.5"/></svg>info@clearvaleglass.com</span>
</div>

<header class="abs site-header">
  <div class="brand"><span class="brand-mark"></span><span class="brand-name">CLEARVALE</span></div>
  <nav class="main-nav">
    <a class="active" style="left:452px">Home</a>
    <a style="left:528px">Products</a>
    <a style="left:643px">Hardware</a>
    <a style="left:763px">Glass</a>
    <a style="left:843px">News</a>
    <a style="left:920px">Blog</a>
    <a style="left:992px">Contact</a>
  </nav>
</header>

<section class="abs hero" role="img" aria-label="Photograph of a curved glass atrium with a lattice glass roof"></section>
<svg class="abs hero-hex" viewBox="0 0 400 465"><polygon points="200,0 400,116 400,349 200,465 0,349 0,116" fill="#1a73d0" fill-opacity=".82"/></svg>
<h1 class="abs hero-title">Clearvale<br>Glass &amp;<br>Hardwares</h1>
<div class="abs hero-dots"><span class="on"></span><span></span><span></span><span></span></div>

<h2 class="abs section-title" style="top:739px">Special Glass</h2>
<svg class="abs title-rule" style="top:786px" viewBox="0 0 324 20"><line x1="0" y1="10" x2="324" y2="10" stroke="#c9c9c9"/><rect x="152" y="0" width="20" height="20" fill="#1e9ad6"/></svg>

<article class="abs glass-card" style="left:120px" role="img" aria-label="Photograph of curved glass architecture" >
  <div style="position:absolute;inset:0;background:linear-gradient(160deg,#9fb7c8,#dfe8ee 55%,#7d93a4)"></div>
  <div class="card-label" style="top:212px">Curve Glass</div>
</article>
<article class="abs glass-card" style="left:449px" role="img" aria-label="Photograph of tinted glass facade reflecting trees">
  <div style="position:absolute;inset:0;background:linear-gradient(160deg,#2d6fb8,#6ea6d8 50%,#1e4f8f)"></div>
  <div class="card-label" style="top:212px">Tinted Glass Thermal</div>
</article>
<article class="abs glass-card" style="left:775px" role="img" aria-label="Photograph of acoustic glass panels against the sky">
  <div style="position:absolute;inset:0;background:linear-gradient(180deg,#1b5fb5,#5d9ee0 55%,#0e2f5a)"></div>
  <div class="card-label" style="top:212px">Acoustic Glass</div>
</article>

<section class="abs about" role="img" aria-label="Photograph of a curved glass walkway tunnel"></section>
<div class="abs about-copy">
  <h2>About Clearvale</h2>
  <h3>Glass &amp; Hardwares</h3>
  <p>Vivamus porttitor purus nisi eleifend libero a tempus libero lectus feugiat felis Morbi diam mauris</p>
  <p>Morbi porta Albero id ullamcorper nonummy nibh ligula pulvinar metus eget consectetuer augue nisi quis lacus Ut ac mi quis lacus mollis aliquam Curabitur iaculis tempus eros</p>
</div>
<a class="abs btn btn-light" style="left:730px;top:1528px">Learn More</a>

<section class="abs hardware"></section>
<h2 class="abs section-title" style="top:1732px">Hard Ware &amp; Products</h2>
<svg class="abs title-rule" style="top:1776px" viewBox="0 0 324 20"><line x1="0" y1="10" x2="324" y2="10" stroke="#c9c9c9"/><rect x="152" y="0" width="20" height="20" fill="#1e9ad6"/></svg>

<svg class="abs slider-arrow" style="left:102px" viewBox="0 0 40 70"><path d="M32 4L6 35l26 31" fill="none" stroke="#1e6fc0" stroke-width="5"/></svg>
<svg class="abs slider-arrow" style="left:1058px" viewBox="0 0 40 70"><path d="M8 4l26 31L8 66" fill="none" stroke="#1e6fc0" stroke-width="5"/></svg>

<article class="abs product-card" style="left:142px" role="img" aria-label="Photograph of a glass office partition">
  <div style="position:absolute;inset:0;background:linear-gradient(180deg,#e3e8ec,#b9c4cc)"></div>
  <div class="card-label" style="top:185px">Glass</div>
</article>
<article class="abs product-card" style="left:377px" role="img" aria-label="Photograph of green glass splash back tiles">
  <div style="position:absolute;inset:0;background:linear-gradient(135deg,#c9ef9a,#6fc83e 50%,#9ee06a)"></div>
  <div class="card-label" style="top:185px">Splash Back</div>
</article>
<article class="abs product-card" style="left:610px" role="img" aria-label="Photograph of a glass pool fence beside blue water">
  <div style="position:absolute;inset:0;background:linear-gradient(180deg,#c3d6e6,#7ab9da 50%,#1f8fc7)"></div>
  <div class="card-label" style="top:185px">Pool Fence</div>
</article>
<article class="abs product-card" style="left:843px" role="img" aria-label="Photograph of a glass balustrade on a terrace">
  <div style="position:absolute;inset:0;background:linear-gradient(180deg,#9aa7a6,#6d6a5c 60%,#4a4639)"></div>
  <div class="card-label" style="top:185px">Balustrade</div>
</article>

<section class="abs why"></section>
<div class="abs why-copy">
  <h2>Why Our Products</h2>
  <p>Vivamus porttitor purus nisi eleifend libero a tempus libero lectus feugiat felis Morbi diam mauris</p>
  <p>Morbi porta Albero id ullamcorper nonummy nibh ligula pulvinar metus eget consectetuer augue nisi quis lacus Ut ac mi quis lacus mollis aliquam Curabitur iaculis tempus eros</p>
</div>
<a class="abs btn btn-blue" style="left:148px;top:2408px">Learn More</a>
<div class="abs why-visual" role="img" aria-label="Photograph of curved clear glass panels standing upright"></div>

<footer class="abs site-footer">
  <div class="brand"><span class="brand-mark"></span><span class="brand-name">CLEARVALE</span></div>
  <div class="social"><span></span><span></span><span></span><span></span></div>
  <div class="foot-col" style="left:464px"><h4>Quick Links</h4><ul><li>Home</li><li>About Us</li><li>Products</li><li>Why Us</li></ul></div>
  <div class="foot-col" style="left:660px;top:72px"><h4>Resources</h4><ul><li>Curve glass</li><li>Tinted glass thermal</li><li>Acoustic glass</li><li>Glass &amp; Mirror</li></ul></div>
  <div class="foot-col" style="left:872px;top:70px"><h4>Contact Us</h4><ul>
    <li><svg viewBox="0 0 16 16"><path d="M8 1a5 5 0 0 0-5 5c0 4 5 9 5 9s5-5 5-9a5 5 0 0 0-5-5z" fill="#1565b0"/><circle cx="8" cy="6" r="2" fill="#fff"/></svg>48 Harbour Row #3</li>
    <li style="padding-left:27px">Lakeport 20417</li>
    <li><svg viewBox="0 0 16 16"><path d="M4 1l3 3-2 2c1 2 3 4 5 5l2-2 3 3-2 2C7 14 2 9 2 3z" fill="none" stroke="#1565b0" stroke-width="1.3"/></svg>555.014.2290</li>
    <li><svg viewBox="0 0 16 16"><rect x="1" y="3" width="14" height="10" fill="none" stroke="#1565b0" stroke-width="1.3"/><path d="M1 3l7 6 7-6" fill="none" stroke="#1565b0" stroke-width="1.3"/></svg>info@clearvaleglass.com</li>
  </ul></div>
</footer>

<div class="abs copyright">© 2018 Company Name&nbsp; All right reserved</div>

</body>
</html>
```